QuillVane needs a dashboard page designed

Redesign the dashboard shown in the provided images.

There are two images:
- dashboard.png
- dashboard-expanded.png

NOTE: The vocabulary navigation on the left will be a very long list of words 100s, so keep that in mind when you're designing both the vocab navigation and the expanded vocab popup.

In the dashboard.png picture, there needs to be a progress chart showing the word progress like the following: review 1(show it as completed) -> review 2(show the user they are here) -> review 3(unvisited) -> review 4(unvisited)

The do-not-design-this-page.png image is for your reference only. It is not to be designed. Use it to understand the overall look and feel of the website to help you create the best dashboard page possible.
Updates

Need extra days to review

Industry/Entity Type

Education English learning

Number of Pages Required

1 page

Requirements
Must have
• The main navigation and main header cannot change between pages. See the do-not-design page for the main navigateion and header.
Should not have
• Do not add a person profile. We will not have images of our users. Keep the icons in the main navigation as they are.

```html
<!DOCTYPE html>
<html lang="en">
<head>
<meta charset="utf-8">
<title>QuillVane – Vocabulary Dashboard</title>
<link href="https://fonts.googleapis.com/css2?family=Albert+Sans:wght@400;500;600;700&display=swap" rel="stylesheet">
<style>
:root{
  --page:#2d373d;
  --frame:#323d43;
  --panel:#263036;
  --rail:#222b30;
  --text:#eef1f3;
  --muted:#cfd4d8;
  --line:#55616a;
  --blue:#2b82e6;
  --green:#4fbf6b;
  --star:#f4b731;
  --point:#e3c6f0;
}
*{box-sizing:border-box;margin:0;padding:0}
html,body{width:1200px;height:892px;overflow:hidden;background:var(--page);font-family:"Albert Sans",sans-serif;color:var(--text)}
.canvas{position:relative;width:1200px;height:892px}
.frame{position:absolute;left:12px;top:16px;width:1176px;height:862px;border-radius:22px;background:var(--frame)}
.topbar{position:absolute;left:19px;top:22px;width:1161px;height:44px;border-radius:22px;background:var(--panel)}
.product{position:absolute;left:25px;top:15px;font-size:12.5px;font-weight:500;letter-spacing:.2px}
.product::after{content:"";display:inline-block;margin-left:7px;vertical-align:middle;border:3.5px solid transparent;border-top:4px solid var(--text);transform:translateY(2px)}
.brand{position:absolute;left:0;right:0;top:12px;text-align:center;font-size:17.5px;font-weight:700}
.tool{position:absolute;top:8px;width:29px;height:29px;border-radius:50%;background:#2d383e;display:flex;align-items:center;justify-content:center}
.sidebar{position:absolute;left:19px;top:76px;width:244px;height:791px;border-radius:16px;background:var(--panel);overflow:hidden}
.rail{position:absolute;left:0;top:0;width:49px;height:100%;background:var(--rail)}
.rail .sep{position:absolute;left:4px;width:41px;height:1px;background:#3a454c}
.rail svg{position:absolute;left:15px}
.filter{position:absolute;left:63px;top:16px;width:54px;height:28px;border-radius:6px;background:#2b363c;font-size:11px;font-weight:500;padding:9px 0 0 9px}
.filter::after{content:"";display:inline-block;margin-left:7px;border:3px solid transparent;border-top:3.5px solid var(--text);vertical-align:middle;transform:translateY(1px)}
.popout{position:absolute;left:203px;top:11px;width:30px;height:30px;border-radius:50%;background:#2d383e;display:flex;align-items:center;justify-content:center}
.group{position:absolute;left:73px;font-size:9.5px;font-weight:600;display:flex;align-items:center;gap:5px}
.help{width:11px;height:11px;border:1px solid var(--text);border-radius:50%;font-size:7px;display:inline-flex;align-items:center;justify-content:center;margin-left:2px}
.word{position:absolute;left:84px;font-size:8px;font-weight:500;color:var(--muted);letter-spacing:.1px}
.card{position:absolute;background:var(--panel);border-radius:18px}
.reviews{left:296px;top:88px;width:856px;height:117px}
.card-title{position:absolute;font-size:17px;font-weight:700;letter-spacing:-.2px}
.step{position:absolute;top:71px;font-size:12px;font-weight:500;color:var(--muted);display:flex;align-items:center;gap:8px}
.arrow{position:absolute;top:72px;width:20px;height:10px}
.dot{width:10px;height:10px;border-radius:50%;border:1px solid var(--muted)}
.dot.current{background:var(--blue);border:1.5px solid #9fc7f4}
.legend{position:absolute;left:703px;font-size:10.5px;font-weight:500;color:var(--muted);display:flex;align-items:center;gap:9px}
.start{position:absolute;left:304px;top:234px;width:283px;height:33px;border:1px solid #8c969d;border-radius:17px;font-size:10.5px;font-weight:500;padding:10px 0 0 15px}
.play{position:absolute;right:6px;top:4px;width:24px;height:24px;border-radius:50%;background:#3b474e;display:flex;align-items:center;justify-content:center}
.current-word{position:absolute;right:30px;top:243px;font-size:14px;font-weight:700;display:flex;align-items:center;gap:7px}
.body-text{position:absolute;left:301px;width:830px;font-size:11px;line-height:24.4px}
.graph{left:296px;top:375px;width:856px;height:368px}
.graph svg{position:absolute;left:0;top:0}
.analysis{position:absolute;left:301px;top:772px;font-size:16.5px;font-weight:700;letter-spacing:-.2px}
</style>
</head>
<body>
<div class="canvas">
  <div class="frame"></div>

  <header class="topbar">
    <div class="product">WORDNEST TUTOR</div>
    <div class="brand">QUILLVANE</div>
    <div class="tool" style="left:1033px">
      <svg width="14" height="14" viewBox="0 0 24 24"><path fill="#fff" d="M12 8a4 4 0 1 0 0 8 4 4 0 0 0 0-8zm9 5.5v-3l-2.6-.6a7 7 0 0 0-.8-1.9l1.4-2.3-2.1-2.1-2.3 1.4a7 7 0 0 0-1.9-.8L12.1 2h-3l-.6 2.6a7 7 0 0 0-1.9.8L4.3 4 2.2 6.1l1.4 2.3a7 7 0 0 0-.8 1.9L.2 11v3l2.6.6c.2.7.4 1.3.8 1.9l-1.4 2.3 2.1 2.1 2.3-1.4c.6.4 1.2.6 1.9.8l.6 2.6h3l.6-2.6c.7-.2 1.3-.4 1.9-.8l2.3 1.4 2.1-2.1-1.4-2.3c.4-.6.6-1.2.8-1.9z" transform="translate(1.3 0)"/><circle cx="13.3" cy="12.5" r="3" fill="#2d383e"/></svg>
    </div>
    <div class="tool" style="left:1077px">
      <svg width="17" height="17" viewBox="0 0 24 24" fill="none" stroke="#fff" stroke-width="2"><path d="M20 12a8 8 0 1 1-4-6.9"/><path d="M8 11l4 4 9-10"/></svg>
    </div>
    <div class="tool" style="left:1121px">
      <svg width="11" height="11" viewBox="0 0 24 24" fill="#fff"><circle cx="12" cy="7" r="5"/><path d="M2 23c0-6 4.5-9 10-9s10 3 10 9z"/></svg>
    </div>
  </header>

  <nav class="sidebar">
    <div class="rail">
      <svg style="top:34px" width="17" height="17" viewBox="0 0 24 24" fill="#fff"><path d="M12 2 1 12h3v10h6v-7h4v7h6V12h3z"/></svg>
      <div class="sep" style="top:83px"></div>
      <svg style="top:106px" width="17" height="17" viewBox="0 0 24 24" fill="#b7c0c6"><path d="M12 1a6 6 0 0 0-6 6c0 4.5 6 10 6 10s6-5.5 6-10a6 6 0 0 0-6-6zm0 8.5A2.5 2.5 0 1 1 12 4.5a2.5 2.5 0 0 1 0 5z"/><path d="M3 23l3-7h3l3 3 3-3h3l3 7z"/></svg>
      <div class="sep" style="top:153px"></div>
      <svg style="top:178px" width="17" height="17" viewBox="0 0 24 24" fill="#b7c0c6"><path d="M2 23V3h9v5h11v15zm2-17v2h2V6zm3 0v2h2V6zM4 10v2h2v-2zm3 0v2h2v-2zm-3 4v2h2v-2zm3 0v2h2v-2zm6-3v2h2v-2zm4 0v2h2v-2zm-4 4v2h2v-2zm4 0v2h2v-2z"/></svg>
    </div>
    <div class="filter">ALL</div>
    <div class="popout">
      <svg width="12" height="12" viewBox="0 0 24 24" fill="none" stroke="#fff" stroke-width="2"><path d="M14 3h7v7M21 3l-9 9M19 14v7H3V5h7"/></svg>
    </div>

    <div class="group" style="top:86px">
      <svg width="9" height="9" viewBox="0 0 24 24" fill="#fff"><circle cx="12" cy="13" r="9"/><circle cx="12" cy="13" r="6" fill="#263036"/><path d="M12 9v4l3 2" stroke="#fff" stroke-width="2"/></svg>
      SHORT-TERM MEMORY <span class="help">?</span>
    </div>
    <div class="word" style="top:113px">GRAB</div>

    <div class="group" style="top:138px">
      <svg width="9" height="9" viewBox="0 0 24 24" fill="#fff"><path d="M2 8h20v13H2zM5 3h14v3H5z"/></svg>
      WORKING MEMORY <span class="help">?</span>
    </div>
    <div class="word" style="top:169px">COOL DOWN</div>
    <div class="word" style="top:193px">CRAVE</div>
    <div class="word" style="top:217px">GO FOR</div>
    <div class="word" style="top:241px">GO-TO</div>
    <div class="word" style="top:264px">IN THE MOOD FOR</div>
    <div class="word" style="top:288px">SIP</div>
    <div class="word" style="top:312px">SOOTHING</div>
    <div class="word" style="top:336px">STICK WITH</div>
    <div class="word" style="top:360px">THROW IN/THROW ON</div>

    <div class="group" style="top:390px">
      <svg width="8" height="9" viewBox="0 0 20 24" fill="#fff"><rect x="1" y="10" width="18" height="13" rx="2"/><path d="M5 10V7a5 5 0 0 1 10 0v3" fill="none" stroke="#fff" stroke-width="2.5"/></svg>
      LONG-TERM MEMORY <span class="help">?</span>
    </div>
    <div class="word" style="top:420px">GIVE IT A TRY</div>
  </nav>

  <section class="card reviews">
    <h2 class="card-title" style="left:29px;top:28px">OUR REVIEWS</h2>
    <div class="step" style="left:30px">
      <svg width="12" height="10" viewBox="0 0 12 10" fill="none" stroke="var(--green)" stroke-width="2"><path d="M1 5l3.5 3.5L11 1"/></svg>REVIEW 1
    </div>
    <svg class="arrow" style="left:135px" viewBox="0 0 20 10" fill="none" stroke="#fff" stroke-width="1.2"><path d="M0 5h19M14 1l5 4-5 4"/></svg>
    <div class="step" style="left:185px"><span class="dot current"></span>REVIEW 2</div>
    <svg class="arrow" style="left:294px" viewBox="0 0 20 10" fill="none" stroke="#fff" stroke-width="1.2"><path d="M0 5h19M14 1l5 4-5 4"/></svg>
    <div class="step" style="left:344px"><span class="dot"></span>REVIEW 3</div>
    <svg class="arrow" style="left:454px" viewBox="0 0 20 10" fill="none" stroke="#fff" stroke-width="1.2"><path d="M0 5h19M14 1l5 4-5 4"/></svg>
    <div class="step" style="left:505px"><span class="dot"></span>REVIEW 4</div>

    <div class="legend" style="top:23px">
      <svg width="11" height="9" viewBox="0 0 12 10" fill="none" stroke="var(--green)" stroke-width="2"><path d="M1 5l3.5 3.5L11 1"/></svg>COMPLETED
    </div>
    <div class="legend" style="top:53px"><span class="dot current"></span>CURRENT STEP</div>
    <div class="legend" style="top:83px"><span class="dot"></span>NOT YET VISITED</div>
  </section>

  <div class="start">START VOCABULARY REVIEW EXERCISE 3
    <span class="play"><svg width="8" height="9" viewBox="0 0 8 9"><path d="M0 0l8 4.5L0 9z" fill="#fff"/></svg></span>
  </div>
  <div class="current-word">GRAB
    <svg width="11" height="11" viewBox="0 0 24 24"><path fill="var(--star)" d="M12 1l3.4 7 7.6 1-5.5 5.3 1.3 7.7L12 18.3 5.2 22l1.3-7.7L1 9l7.6-1z"/></svg>
  </div>

  <p class="body-text" style="top:282px">The word "grab" is most commonly used as a verb, meaning to take something quickly or suddenly, Imagine you're running late for school. You don't have time for breakfast, so you quickly grab an apple from the kitchen and rush out the door. As you reach the bus stop, your friend waves and says, "Hey! Let's grab a coffee after class. Later, when you sit down, your phone starts ringing. You grab it from your bag and answer.</p>

  <section class="card graph">
    <svg width="856" height="368" viewBox="0 0 856 368" font-family="Albert Sans, sans-serif" fill="#eef1f3">
      <text x="22" y="50" font-size="17" font-weight="700">LEARNING CURVE GRAPH</text>
      <g font-size="7.6" font-weight="500" text-anchor="end">
        <text x="75" y="77">LONG-TERM</text><text x="75" y="92">MEMORY</text>
        <text x="75" y="158">WORKING</text><text x="75" y="173">MEMORY</text>
        <text x="75" y="213">SHORT-TERM</text><text x="75" y="228">MEMORY</text>
        <text x="75" y="268">FORGOTTEN</text><text x="75" y="283">MEMORY</text>
      </g>
      <line x1="87.5" y1="90" x2="87.5" y2="289" stroke="#55616a" stroke-width="1"/>
      <line x1="87.5" y1="289" x2="827" y2="289" stroke="#55616a" stroke-width="1"/>
      <g stroke="#d9dde0" stroke-width=".7" stroke-dasharray="2 2" fill="none">
        <path d="M179 206V289"/><path d="M179 206L277.5 289"/>
        <path d="M277.5 114V289"/><path d="M277.5 114L480.6 289"/>
      </g>
      <circle cx="179" cy="206" r="2.6" fill="var(--point)"/>
      <circle cx="277.5" cy="114" r="2.6" fill="var(--point)"/>
      <g font-size="7.6" font-weight="500" text-anchor="middle">
        <text x="170" y="195">18 MAY</text>
        <text x="269" y="101">19 MAY</text>
      </g>
      <g font-size="7.6" font-weight="500" text-anchor="middle">
        <text x="101" y="310">18 MAY</text><text x="152" y="310">12:00</text>
        <text x="201" y="310">19 MAY</text><text x="251" y="310">12:00</text>
        <text x="302" y="310">20 MAY</text><text x="353" y="310">12:00</text>
        <text x="403" y="310">21 MAY</text><text x="453" y="310">12:00</text>
        <text x="503" y="310">22 MAY</text><text x="554" y="310">12:00</text>
        <text x="604" y="310">23 MAY</text><text x="655" y="310">12:00</text>
        <text x="706" y="310">24 MAY</text><text x="756" y="310">12:00</text>
        <text x="802" y="310">25 ...</text>
      </g>
      <text x="417" y="338" font-size="9.5" font-weight="700" text-anchor="middle">DATE RANGE</text>
    </svg>
  </section>

  <h2 class="analysis">WORDNEST TUTOR LEARNING ANALYSIS</h2>
  <p class="body-text" style="top:807px">Lorem ipsum dolor sit amet, consectetur adipiscing elit. Nam rutrum commodo enim id bibendum. Nunc dignissim risus erat, nec finibus nunc dictum eu. Aliquam sit amet euismod metus, quis malesuada erat. Sed at felis quis nulla feugiat cursus at at dolor.</p>
</div>
</body>
</html>
```